MRT Property - Business Cards

Looking for a business card & general letterhead, signage etc design for our new logo.

Colours:
000a20
0056a2
00b5ef
0088ce
68cef2

Fonts:
Poppins
Karla

Please keep look and feel of new brand - example in the zip package I sent.

```html
<!DOCTYPE html>
<html lang="en">
<head>
<meta charset="utf-8">
<title>MRT Property – Business Cards</title>
<link rel="stylesheet" href="https://fonts.googleapis.com/css2?family=Poppins:wght@400;500;600;700&display=swap">
<style>
  :root {
    --ink: #000a20;
    --navy: #0056a2;
    --mid-blue: #0088ce;
    --cyan: #00b5ef;
    --sky: #68cef2;
    --paper: #ffffff;
    --text: #1e1e1e;
    --backdrop: #3b3b3d;
  }
  * { box-sizing: border-box; margin: 0; padding: 0; }
  html, body { width: 1093px; height: 1200px; overflow: hidden; }
  body {
    background: var(--backdrop);
    font-family: "Poppins", sans-serif;
    position: relative;
  }
  .card {
    position: absolute;
    left: 264px;
    width: 578px;
    height: 357px;
    border-radius: 24px;
    overflow: hidden;
  }
  .card-front { top: 226px; background: linear-gradient(100deg, #f1f5fa 0%, var(--paper) 45%); }
  .card-back {
    top: 621px;
    background:
      radial-gradient(ellipse 70% 80% at 85% 40%, var(--sky) 0%, rgba(104,206,242,0) 70%),
      linear-gradient(160deg, var(--cyan) 0%, var(--mid-blue) 55%, #0a5fa0 80%, var(--ink) 115%);
  }

  .id-marker {
    position: absolute; left: 0; top: 46px;
    width: 14px; height: 34px; background: var(--navy);
  }
  .person { position: absolute; left: 26px; top: 42px; }
  .person-name { font-size: 23px; font-weight: 600; color: var(--navy); line-height: 1.1; letter-spacing: 0.2px; }
  .person-role { font-size: 17.5px; font-weight: 400; color: var(--text); line-height: 1.15; }

  .brand {
    position: absolute; right: 28px; top: 56px;
    display: flex; align-items: center; gap: 10px;
  }
  .brand-square { width: 22px; height: 22px; background: var(--mid-blue); }
  .brand-name { font-size: 32px; font-weight: 600; color: var(--navy); line-height: 1; }

  .contact { position: absolute; left: 26px; top: 264px; list-style: none; }
  .contact li {
    display: flex; align-items: center; gap: 7px;
    font-size: 17.5px; color: var(--text); line-height: 21px;
  }
  .contact svg { width: 16px; height: 16px; flex: none; }
  .icon-solid { fill: var(--navy); }
  .icon-line { fill: none; stroke: var(--navy); stroke-width: 2; }
  .contact .accent { color: var(--navy); }

  .address {
    position: absolute; right: 28px; top: 285px;
    text-align right;
    text-align: right; font-size: 17.5px; line-height: 21px; color: var(--text);
    font-style: normal;
  }

  .band { position: absolute; left: 0; bottom: 0; width: 100%; height: 11px; display: flex; }
  .band span:nth-child(1) { width: 176px; background: var(--navy); }
  .band span:nth-child(2) { width: 209px; background: var(--mid-blue); }
  .band span:nth-child(3) { flex: 1; background: var(--cyan); }

  .back-brand {
    position: absolute; inset: 0;
    display: flex; align-items: center; justify-content: center; gap: 16px;
  }
  .back-brand .brand-square { width: 40px; height: 40px; background: var(--paper); }
  .back-brand .brand-name { font-size: 60px; color: var(--paper); }
</style>
</head>
<body>
  <section class="card card-front" aria-label="Business card front">
    <div class="id-marker"></div>
    <div class="person">
      <h1 class="person-name">DANIEL HARTLEY</h1>
      <p class="person-role">Managing Director</p>
    </div>

    <div class="brand">
      <span class="brand-square"></span>
      <span class="brand-name">MRT Property</span>
    </div>

    <ul class="contact">
      <li>
        <svg class="icon-solid" viewBox="0 0 24 24"><path d="M6.6 10.8a15.1 15.1 0 0 0 6.6 6.6l2.2-2.2c.3-.3.7-.4 1-.2 1.1.4 2.3.6 3.6.6.6 0 1 .4 1 1V20c0 .6-.4 1-1 1A17 17 0 0 1 3 4c0-.6.4-1 1-1h3.5c.6 0 1 .4 1 1 0 1.3.2 2.5.6 3.6.1.3 0 .7-.2 1z"/></svg>
        044-987 654 321
      </li>
      <li>
        <svg viewBox="0 0 24 24"><path d="M2 5h20v14H2z" fill="var(--navy)"/><path d="M3 6.5 12 13l9-6.5M3 18l6.5-6M21 18l-6.5-6" fill="none" stroke="#fff" stroke-width="1.4"/></svg>
        hello@mrtprop.com
      </li>
      <li>
        <svg class="icon-line" viewBox="0 0 24 24"><circle cx="12" cy="12" r="9"/><path d="M3 12h18M4.5 7.5h15M4.5 16.5h15M12 3c3.2 3 3.2 15 0 18M12 3c-3.2 3-3.2 15 0 18"/></svg>
        <span>www.<span class="accent">mrtproperty</span>.com</span>
      </li>
    </ul>

    <address class="address">
      88, Harbour View Road<br>
      30571,Northland Bay
    </address>

    <div class="band"><span></span><span></span><span></span></div>
  </section>

  <section class="card card-back" aria-label="Business card back">
    <div class="back-brand">
      <span class="brand-square"></span>
      <span class="brand-name">MRT Property</span>
    </div>
  </section>
</body>
</html>
```